Keystone Trench Co Business Card*

Looking for a professional, clean and crisp business card

I am in the underground utilities industry and am just looking for a really impressive business card. I would like our card to be white with our symbol crisp and clear with it protruding. I also have a business partner that will require his name and info on the card once the design is set. I would like to have our website info on the card which is;
http://keystonetrenchco.example/

Contact Information for Business Card

Website, contact name, number and email

```html
<!DOCTYPE html>
<html lang="en">
<head>
<meta charset="utf-8">
<title>Keystone Trench Co — Business Card</title>
<link rel="stylesheet" href="https://fonts.googleapis.com/css2?family=Oswald:wght@500;600&family=Montserrat:wght@400;500&display=swap">
<style>
  :root {
    --stage: #2a2a2a;
    --stage-dark: #111111;
    --card-black: #050607;
    --card-white: #ffffff;
    --slate: #323d4b;
    --slate-line: #5a6573;
    --ink: #2b3440;
    --body-ink: #222222;
    --accent-blue: #2f56a8;
    --logo-white: #ffffff;
  }
  * { margin: 0; padding: 0; box-sizing: border-box; }
  html, body {
    width: 1200px; height: 900px; overflow: hidden;
  }
  body {
    background: radial-gradient(ellipse at 60% 30%, var(--stage) 0%, var(--stage-dark) 80%);
    position: relative;
    font-family: "Montserrat", sans-serif;
  }
  .card {
    position: absolute;
    left: 220px;
    width: 760px;
    height: 410px;
    overflow: hidden;
    box-shadow: 0 18px 40px rgba(0,0,0,0.55);
  }
  .card--back { top: 30px; background: var(--card-black); }
  .card--front { top: 465px; background: var(--card-black); }

  .pipe-pattern {
    position: absolute; inset: 0;
    background: linear-gradient(135deg, #0a0b0d 0%, #16181c 35%, #0b0c0e 55%, #1a1c20 75%, #08090a 100%);
  }
  .brand {
    position: absolute;
    display: flex; align-items: center; gap: 14px;
    color: var(--logo-white);
    font-family: "Oswald", sans-serif;
    font-weight: 600;
    text-transform: uppercase;
    letter-spacing: 1px;
    white-space: nowrap;
  }
  .brand__dot {
    border: 3px solid var(--logo-white);
    border-radius: 50%;
    flex: none;
  }
  .card--back .brand {
    left: 50%; top: 50%; transform: translate(-50%, -50%);
    font-size: 40px;
  }
  .card--back .brand__dot { width: 34px; height: 34px; }

  .front-shapes { position: absolute; inset: 0; }
  .card--front .brand {
    right: 44px; top: 50%; transform: translateY(-50%);
    font-size: 32px;
  }
  .card--front .brand__dot { width: 28px; height: 28px; }

  .contact {
    position: absolute;
    left: 30px; bottom: 46px;
    color: var(--ink);
    z-index: 1;
  }
  .contact__name {
    font-family: "Oswald", sans-serif;
    font-weight: 600;
    font-size: 30px;
    letter-spacing: 1px;
    text-transform: uppercase;
    margin-bottom: 12px;
    white-space: nowrap;
  }
  .contact__line {
    display: flex; align-items: center; gap: 9px;
    font-size: 15px;
    line-height: 1.55;
    color: var(--body-ink);
    white-space: nowrap;
  }
  .contact__line svg { width: 17px; height: 17px; flex: none; }
  .contact__web-main { color: var(--accent-blue); }
</style>
</head>
<body>

  <section class="card card--back">
    <div class="pipe-pattern" role="img" aria-label="Dark diagonal pipe pattern background"></div>
    <div class="brand"><span class="brand__dot"></span>Keystone Trench Co</div>
  </section>

  <section class="card card--front">
    <svg class="front-shapes" viewBox="0 0 760 410" preserveAspectRatio="none" aria-hidden="true">
      <polygon points="0,0 70,0 500,410 0,410" fill="var(--slate)"/>
      <polygon points="0,0 10,0 440,410 0,410" fill="var(--card-white)"/>
      <line x1="74" y1="0" x2="504" y2="410" stroke="var(--slate-line)" stroke-width="1.5"/>
    </svg>

    <div class="contact">
      <h1 class="contact__name">Dale Marchetti</h1>
      <p class="contact__line">
        <svg viewBox="0 0 24 24" fill="none" stroke="var(--accent-blue)" stroke-width="1.8"><circle cx="12" cy="12" r="10"/><path d="M8.5 7.5c0 4.5 3.5 8 8 8l1-2-2.5-1.2-1.2 1.2c-1.5-.7-2.6-1.8-3.3-3.3l1.2-1.2L10.5 6.5z"/></svg>
        778-555-0142
      </p>
      <p class="contact__line">
        <svg viewBox="0 0 24 24" fill="none" stroke="var(--accent-blue)" stroke-width="1.8"><rect x="2" y="5" width="20" height="14"/><path d="M2 5l10 8 10-8"/></svg>
        dale@keystonetrenchco.example
      </p>
      <p class="contact__line">
        <svg viewBox="0 0 24 24" fill="none" stroke="var(--accent-blue)" stroke-width="1.8"><circle cx="12" cy="12" r="10"/><path d="M2 12h20M12 2c3 3 3 17 0 20M12 2c-3 3-3 17 0 20"/></svg>
        <span>www.<span class="contact__web-main">keystonetrenchco</span>.example</span>
      </p>
    </div>

    <div class="brand"><span class="brand__dot"></span>Keystone Trench Co</div>
  </section>

</body>
</html>
```